Summit Builders Web Site / Business Cards

Construction Company that specializes in Water and Fire Damage, Residential ReModels, Landscaping and Building ADU (Accessory Dwelling Unit)

Growing and changing families often need additional space, and a remodeling project can often provide that. Adding a new area, or repurposing an existing one can satisfy this requirement.

Other times, homeowners want to update the look in their kitchen or bathroom with more than just a change of cabinetry or vanity doors and drawers. Whatever your needs are, Summit Builders has skilled workers who are bonded and insured, and ready to make your dreams and visions a reality.

Target Market(s)

Home Owners

Industry/Entity Type

Construction Company

Contact Information for Business Card

Center Logo with our information on the corners

Back side to be Logo Only
Contact Info
CSLB License # 2418596
info@summitbuildersca.example
www.summitbuildersca.example

Coding

Coded - Design and coding required

Number of Pages Required

5+ page

Font styles to use
Serif
Sans Serif

Requirements
Must have
• Using our Logo Colors
Home
About Us
Services
Projects / Portfolio
Contact Us
Nice to have
• Colors matching our Logo
Should not have
• Black because it doesnt match our logo

```html
<!DOCTYPE html>
<html lang="en">
<head>
<meta charset="utf-8">
<title>Summit Builders</title>
<link href="https://fonts.googleapis.com/css2?family=Montserrat:wght@400;500;600;700&family=Lato:wght@400;700&display=swap" rel="stylesheet">
<style>
:root{
  --orange:#ff6a00;
  --orange-soft:#ff8a33;
  --navy:#141b2e;
  --ink:#2a2a2a;
  --muted:#6b6b6b;
  --faint:#ececec;
  --line:#e2e2e2;
  --white:#ffffff;
  --dark-band:#2b2a33;
}
*{box-sizing:border-box;margin:0;padding:0}
html,body{width:1200px;height:4471px;overflow:hidden}
body{position:relative;background:var(--white);font-family:"Lato",sans-serif;color:var(--ink)}
.abs{position:absolute}
.heading-font{font-family:"Montserrat",sans-serif}
.center{text-align:center}
.btn{position:absolute;display:flex;align-items:center;justify-content:center;font-family:"Montserrat",sans-serif;font-size:12px;color:var(--white);background:var(--orange);border-radius:2px}
.btn-outline{background:transparent;border:1px solid var(--orange);color:var(--orange)}

/* hero */
.hero{left:0;top:0;width:1200px;height:674px;background:linear-gradient(100deg,#3a2a22 0%,#6a3b1e 30%,#b8621f 55%,#e07422 75%,#7a3f1a 100%)}
.nav a{position:absolute;top:30px;font-family:"Montserrat",sans-serif;font-size:13px;color:var(--white);text-decoration:none}
.nav .active{color:var(--orange-soft);border-bottom:2px solid var(--orange);padding-bottom:8px}
.logo-tab{left:537px;top:0;width:126px;height:106px}
.logo-name{left:537px;top:36px;width:126px;font-family:"Montserrat",sans-serif;font-weight:700;font-size:14px;line-height:16px;color:var(--navy);text-align:center}
.hero-box{left:347px;top:196px;width:504px;height:313px;background:rgba(30,30,34,.78)}
.hero-title{left:347px;top:228px;width:504px;font-family:"Montserrat",sans-serif;font-weight:700;font-size:36px;color:var(--white)}
.hero-title2{left:347px;top:274px;width:504px;font-family:"Montserrat",sans-serif;font-weight:700;font-size:37px;color:var(--orange)}
.hero-text{left:380px;top:336px;width:440px;font-size:13px;line-height:21px;color:var(--white)}
.dots span{position:absolute;left:201px;width:5px;height:5px;border-radius:50%;background:var(--white)}
.social-side span{position:absolute;left:985px;width:16px;height:16px;border-radius:50%;background:var(--white)}

/* section titles */
.ghost{left:0;width:1200px;font-family:"Montserrat",sans-serif;font-weight:700;font-size:38px;color:var(--faint);text-align:center;text-shadow:0 2px 6px rgba(0,0,0,.12)}
.title{left:0;width:1200px;font-family:"Montserrat",sans-serif;font-weight:700;font-size:30px;color:var(--ink);text-align:center}
.title em{font-style:normal;color:var(--orange)}
.lead{left:300px;width:600px;font-size:12px;line-height:21px;color:var(--muted);text-align:center}

/* about */
.about-card{left:193px;top:849px;width:531px;height:294px;background:var(--white);box-shadow:0 2px 12px rgba(0,0,0,.14)}
.bar{height:37px;display:flex;align-items:center;justify-content:space-between;padding:0 16px;font-family:"Montserrat",sans-serif;font-weight:600;font-size:14px}
.bar-orange{background:var(--orange);color:var(--white)}
.about-photo{left:14px;top:54px;width:217px;height:221px;background:linear-gradient(160deg,#8a6a45,#3c2d20 60%,#1f1a16)}
.about-text h3{font-family:"Montserrat",sans-serif;font-size:14px;font-weight:600;margin-bottom:10px}
.about-text p{font-size:10.5px;line-height:17px;color:var(--muted)}
.mission-bar{left:193px;top:1162px;width:531px;height:37px;background:var(--white);box-shadow:0 2px 10px rgba(0,0,0,.14)}
.quote-card{left:756px;top:849px;width:250px;height:294px;background:#f4f4f4}
.quote-head{background:var(--navy);color:var(--white);justify-content:center}
.field{position:absolute;left:15px;width:219px;height:27px;background:var(--white);border:1px solid var(--line);font-size:9px;color:#888;padding:8px 14px}

/* partners */
.partners{left:0;top:1280px;width:1200px;height:197px;background:linear-gradient(120deg,#26232e,#4a4658 50%,#25222c)}
.partner-strip{left:193px;top:1329px;width:813px;height:87px;background:var(--white)}
.partner-badge{position:absolute;top:24px;height:40px;background:#d9dde6;border-radius:3px}
.arrow-circle{position:absolute;top:1360px;width:24px;height:24px;border-radius:50%;background:var(--white);border:1px solid var(--orange)}

/* services */
.svc{position:absolute;top:1741px;width:245px;height:281px;background:var(--white);box-shadow:0 2px 12px rgba(0,0,0,.12);padding:24px 12px}
.svc h4{font-family:"Montserrat",sans-serif;font-size:14px;font-weight:600;color:var(--orange);margin-bottom:24px}
.svc p{font-size:9.5px;line-height:16px;color:var(--muted)}
.svc .more{position:absolute;left:12px;bottom:38px;font-size:13px;color:var(--orange)}
.svc.featured{top:1732px;height:300px;background:var(--orange);padding:30px 30px}
.svc.featured h4,.svc.featured p,.svc.featured .more{color:var(--white)}
.svc.featured .more{left:30px}
.svc-icon{position:absolute;right:14px;bottom:24px}

/* testimonials */
.band{left:0;top:2366px;width:1200px;height:306px;background:linear-gradient(120deg,#2f2b30,#3f3a3b 50%,#262428)}
.avatar{left:550px;top:2316px;width:100px;height:100px;border-radius:50%;background:linear-gradient(#c9c2ba,#8b7f74);border:4px solid var(--white)}

/* gallery */
.tile{position:absolute;background:linear-gradient(140deg,#7f8fa8,#c9a57a 60%,#8a6a4a)}

/* footer */
.footer{left:0;top:3992px;width:1200px;height:479px;background:linear-gradient(180deg,#2f2b28,#3c332b 60%,#2a2420)}
.foot-h{font-family:"Montserrat",sans-serif;font-size:20px;font-weight:600;color:var(--white)}
.foot-t{font-family:"Montserrat",sans-serif;font-size:11px;color:var(--white)}
.foot-links a{display:block;font-family:"Montserrat",sans-serif;font-size:10px;color:var(--white);text-decoration:none;margin-bottom:12px}
.social-foot span{position:absolute;top:4372px;width:28px;height:28px;border-radius:50%;border:2px solid var(--white)}
</style>
</head>
<body>

<!-- HERO -->
<header class="abs hero" role="img" aria-label="Construction site scaffolding photo in warm orange light"></header>
<nav class="nav">
  <a class="active" style="left:238px">Home</a>
  <a style="left:316px">About Us</a>
  <a style="left:417px">Our Services</a>
  <a style="left:700px">Gallery</a>
  <a style="left:787px">Contact Us</a>
</nav>
<div class="btn" style="left:900px;top:23px;width:108px;height:29px">Get A Quote</div>
<svg class="abs logo-tab" viewBox="0 0 126 106"><polygon points="0,0 126,0 126,86 63,106 0,86" fill="#fff"/><rect x="55" y="12" width="16" height="16" fill="#ff6a00"/></svg>
<div class="abs logo-name">SUMMIT<br>BUILDERS</div>

<div class="abs hero-box"></div>
<div class="abs hero-title center">Welcome to</div>
<div class="abs hero-title2 center">Summit Builders</div>
<p class="abs hero-text center">Construction Company that specializes in Water and Fire Damage, Residential ReModels, Landscaping and Building ADU (Accessory Dwelling Unit)</p>
<div class="btn" style="left:478px;top:429px;width:112px;height:29px;font-size:10px">Explore Services</div>
<div class="btn btn-outline" style="left:610px;top:429px;width:111px;height:29px;font-size:10px">Contact Us</div>

<div class="dots"><span style="top:298px"></span><span style="top:318px"></span><span style="top:334px;left:197px;width:13px;height:13px;background:transparent;border:2px solid #fff"></span><span style="top:356px"></span><span style="top:372px"></span></div>
<div class="social-side"><span style="top:280px"></span><span style="top:330px"></span><span style="top:381px"></span></div>
<div class="abs" style="left:590px;top:553px;width:20px;height:26px;border:2px solid var(--orange);border-radius:3px"></div>

<!-- WHO WE ARE -->
<div class="abs ghost" style="top:724px">Few Words About Our Mission &amp; Vision</div>
<div class="abs heading-font" style="left:193px;top:781px;font-size:30px;font-weight:700">Who <span style="color:var(--orange)">We</span> Are</div>
<div class="abs" style="left:396px;top:800px;width:610px;height:1px;background:var(--orange)"></div>
<div class="btn btn-outline" style="left:756px;top:782px;width:112px;height:36px;background:#fff">Read More</div>

<section class="abs about-card">
  <div class="bar bar-orange"><span>About Us</span><span>—</span></div>
  <div class="abs about-photo" role="img" aria-label="Heavy mining machinery at a work site"></div>
  <div class="abs about-text" style="left:250px;top:58px;width:266px">
    <h3>What is Summit Builders?</h3>
    <p>Lorem Ipsum is simply dummy text of the printing and typesetting industry. Lorem Ipsum has been the industry's standard dummy text ever since the 1500s, when an unknown printer took a galley of type and scrambled it to make a type specimen book. It has survived not only five centuries, but also the leap into electronic typesetting, remaining essentially unchanged. It was popularised in the 1960s with the release of Letraset sheets containing Lorem Ipsum passages, and more recently with desktop publishing software like.</p>
  </div>
</section>
<div class="abs mission-bar bar" style="display:flex"><span>Our Mission and Vision</span><span style="font-size:22px;font-weight:400">+</span></div>

<section class="abs quote-card">
  <div class="bar quote-head">Get A Free Quote</div>
  <div class="field" style="top:52px">Your Name</div>
  <div class="field" style="top:92px">Your Email Address</div>
  <div class="field" style="top:132px">Your Phone Number</div>
  <div class="field" style="top:172px">Quote Subject</div>
  <div class="field" style="top:211px;height:81px">Your Message</div>
</section>
<div class="btn" style="left:756px;top:1162px;width:250px;height:37px;font-size:14px;font-weight:600">Submit Now</div>

<!-- PARTNERS -->
<div class="abs partners" role="img" aria-label="Building framework silhouette at dusk"></div>
<div class="abs partner-strip">
  <div class="partner-badge" style="left:26px;width:100px"></div>
  <div class="partner-badge" style="left:186px;width:100px;height:20px;top:34px"></div>
  <div class="partner-badge" style="left:380px;width:80px"></div>
  <div class="partner-badge" style="left:558px;width:40px;border-radius:50%"></div>
  <div class="partner-badge" style="left:672px;width:110px;height:26px;top:31px"></div>
</div>
<div class="arrow-circle" style="left:181px"></div>
<div class="arrow-circle" style="left:994px"></div>
<svg class="abs" style="left:0;top:1430px" width="1200" height="48" viewBox="0 0 1200 48"><path d="M0 48 L470 48 C540 48 540 12 600 12 C660 12 660 48 730 48 L1200 48 Z" fill="#fff"/><path d="M588 32 L600 42 L612 32" stroke="#ff6a00" stroke-width="2" fill="none"/></svg>

<!-- SERVICES -->
<div class="abs ghost" style="top:1520px">Some Of Our Services</div>
<div class="abs title" style="top:1574px">Our <em>Services</em></div>
<p class="abs lead" style="top:1630px">It is a long established fact that a reader will be distracted by the readable content of a page when looking at its layout. The point of using Lorem Ipsum is that it has a more-or-less normal distribution of letters, as opposed to using 'Content here.</p>

<article class="svc" style="left:193px">
  <h4>Water and Fire Damage</h4>
  <p>Lorem ipsum dolor sit amet, consectetur adipiscing elit. Pretium arcu duis enim sit lorem non. Nunc, maecenas laoreet vitae urna felis turpis quis. Lectus duis penatibus gravida id gravida vestibulum, gravida ut id. Consectetur dictum quisque magnis eget odio euismod pellentesque. Dignissim vel elementum auctor et netus aliquam euismod.</p>
  <span class="more">Read More →</span>
  <svg class="svc-icon" width="30" height="36" viewBox="0 0 30 36"><path d="M15 2 C22 12 27 18 27 24 A12 12 0 0 1 3 24 C3 18 9 12 15 2Z" fill="none" stroke="#333" stroke-width="2"/></svg>
</article>
<article class="svc featured" style="left:459px;width:281px">
  <h4>Residential ReModels</h4>
  <p>Lorem ipsum dolor sit amet, consectetur adipiscing elit. Pharetra dictumst quisque sollicitudin purus elit. Fames leo volutpat, ac justo, tellus. Consequat cras quis sapien ac sed quis. Placerat vehicula metus, id pellentesque adipiscing ullamcorper ultricies id augue integer hac dolor, eget ornare molestie elementum. Porttitor dictum viverra.</p>
  <span class="more">Read More →</span>
  <svg class="svc-icon" style="right:28px" width="38" height="36" viewBox="0 0 38 36"><path d="M3 17 L19 4 L35 17 M7 14 V33 H31 V14 M14 33 V23 H24 V33" fill="none" stroke="#fff" stroke-width="2"/></svg>
</article>
<article class="svc" style="left:761px">
  <h4>Landscaping and Building</h4>
  <p>Lorem ipsum dolor sit amet, consectetur adipiscing elit. Pharetra dictumst quisque sollicitudin purus elit. Fames leo volutpat, ac justo, tellus. Consequat cras quis sapien ac sed quis. Placerat vehicula metus, id pellentesque adipiscing ullamcorper ultricies id augue integer hac dolor, eget ornare molestie elementum. Porttitor dictum viverra.</p>
  <span class="more">Read More →</span>
  <svg class="svc-icon" width="30" height="38" viewBox="0 0 30 38"><rect x="4" y="3" width="22" height="33" fill="none" stroke="#333" stroke-width="2"/><path d="M9 9h4v4H9zM17 9h4v4h-4zM9 17h4v4H9zM17 17h4v4h-4zM12 27h6v9h-6z" fill="none" stroke="#333" stroke-width="1.6"/></svg>
</article>
<div class="btn" style="left:537px;top:2083px;width:125px;height:36px">Read More</div>

<!-- TESTIMONIALS -->
<div class="abs ghost" style="top:2178px">What Our Client Says</div>
<div class="abs title" style="top:2239px">Our <em>Testimonials</em></div>
<div class="abs band" role="img" aria-label="Construction machinery silhouette at dusk"></div>
<div class="abs avatar" role="img" aria-label="Client portrait"></div>
<div class="abs heading-font center" style="left:0;top:2434px;width:1200px;font-size:15px;color:var(--orange)">Marco Lenz</div>
<div class="abs center" style="left:0;top:2461px;width:1200px;font-size:12px;color:var(--white)">CEO Company Name</div>
<p class="abs lead" style="left:295px;top:2510px;width:610px;color:#ddd">It is a long established fact that a reader will be distracted by the readable content of a page when looking at its layout. The point of using Lorem Ipsum is that it has a more-or-less normal distribution of letters, as opposed to using 'Content here.</p>
<svg class="abs" style="left:550px;top:2604px" width="100" height="24" viewBox="0 0 100 24"><g fill="#fff"><circle cx="11" cy="12" r="2.5"/><circle cx="30" cy="12" r="2.5"/><circle cx="50" cy="12" r="3"/><circle cx="70" cy="12" r="2.5"/><circle cx="89" cy="12" r="2.5"/></g><circle cx="50" cy="12" r="9" fill="none" stroke="#fff" stroke-width="1.5"/></svg>

<!-- GALLERY -->
<div class="abs ghost" style="top:2722px">Work We Have Done Already</div>
<div class="abs title" style="top:2781px">Our <em>Gallery</em></div>
<p class="abs lead" style="top:2839px">It is a long established fact that a reader will be distracted by the readable content of a page when looking at its layout. The point of using Lorem Ipsum is that it has a more-or-less normal distribution of letters, as opposed to using 'Content here.</p>

<div class="tile" style="left:31px;top:2950px;width:266px;height:267px" role="img" aria-label="Workers on a rebar foundation"></div>
<div class="tile" style="left:321px;top:2950px;width:556px;height:267px;background:linear-gradient(140deg,#c99a5e,#e8c890 50%,#8a6a3a)" role="img" aria-label="Workers cutting boards on a deck"></div>
<div class="tile" style="left:902px;top:2950px;width:267px;height:267px;background:linear-gradient(160deg,#d8d2c6,#a59a88)" role="img" aria-label="Interior renovation in progress"></div>
<div class="tile" style="left:31px;top:3241px;width:266px;height:268px;background:linear-gradient(180deg,#5a8ad0,#d07030 65%,#9a7a5a)" role="img" aria-label="Orange excavator on a site"></div>
<div class="tile" style="left:321px;top:3241px;width:266px;height:268px;background:linear-gradient(160deg,#6a645c,#3f3a35)" role="img" aria-label="House under construction">
  <div class="abs" style="left:20px;top:20px;width:226px;height:228px;border:1px solid rgba(255,255,255,.5)"></div>
  <svg class="abs" style="left:118px;top:110px" width="32" height="32" viewBox="0 0 32 32"><circle cx="14" cy="14" r="10" fill="none" stroke="#fff" stroke-width="2"/><path d="M21 21 L29 29 M14 9v10M9 14h10" stroke="#fff" stroke-width="2"/></svg>
  <div class="abs center" style="left:0;top:150px;width:266px;font-size:14px;color:#fff">Click For Details</div>
</div>
<div class="tile" style="left:611px;top:3241px;width:558px;height:268px;background:linear-gradient(180deg,#6a9ad8,#e8eef4 55%,#9a9a92)" role="img" aria-label="Large white two-storey house"></div>
<div class="tile" style="left:31px;top:3531px;width:556px;height:268px;background:linear-gradient(140deg,#dfe4ea,#3d6aa8 55%,#c03a3a)" role="img" aria-label="Engineers reviewing plans"></div>
<div class="tile" style="left:611px;top:3531px;width:266px;height:268px;background:linear-gradient(150deg,#5f7a94,#d06a2a 50%,#2e3a48)" role="img" aria-label="Worker carrying a pipe"></div>
<div class="tile" style="left:902px;top:3531px;width:267px;height:268px;background:linear-gradient(180deg,#4a86d0,#e07a2a 65%,#a8906a)" role="img" aria-label="Orange wheel loader"></div>
<div class="btn" style="left:537px;top:3863px;width:125px;height:36px">View More</div>

<!-- FOOTER -->
<footer class="abs footer" role="img" aria-label="Dusk silhouette of heavy machinery"></footer>
<div class="abs heading-font center" style="left:0;top:4046px;width:1200px;font-size:30px;font-weight:600;color:#fff">Get In Touch</div>
<div class="abs foot-h" style="left:193px;top:4132px">Our Address</div>
<div class="abs foot-h" style="left:521px;top:4132px">Quick Links</div>
<div class="abs foot-h" style="left:752px;top:4132px">Newsletter</div>

<svg class="abs" style="left:193px;top:4190px" width="12" height="14" viewBox="0 0 12 14"><path d="M6 13 C2 8 1 6 1 5 A5 5 0 0 1 11 5 C11 6 10 8 6 13Z" fill="#ff6a00"/></svg>
<div class="abs foot-t" style="left:214px;top:4190px;width:240px;line-height:18px">Your Address. 12 Ridgeline Avenue,<br>Fairview 0055.</div>
<svg class="abs" style="left:193px;top:4252px" width="12" height="12" viewBox="0 0 12 12"><path d="M2 1 L4.5 1 L5.5 4 L4 5 C5 7 6 8 7 8.5 L8 7 L11 8 L11 10.5 C6 11 1 6 2 1Z" fill="#ff6a00"/></svg>
<div class="abs foot-t" style="left:214px;top:4251px">+00 555 010 2024</div>
<svg class="abs" style="left:193px;top:4294px" width="12" height="10" viewBox="0 0 12 10"><rect x="0.5" y="0.5" width="11" height="9" fill="#ff6a00"/><path d="M1 1 L6 5 L11 1" stroke="#3a2f28" fill="none"/></svg>
<div class="abs foot-t" style="left:214px;top:4292px">info@summitbuilders.example</div>

<div class="abs foot-links" style="left:521px;top:4190px"><a>Home</a><a>About Us</a><a>Our Services</a><a>Gallery</a><a>Contact Us</a></div>

<div class="abs" style="left:752px;top:4191px;width:254px;height:31px;border:1px solid rgba(255,255,255,.45);font-size:10px;color:#fff;padding:9px 12px">Enter Your Email Address</div>
<div class="btn" style="left:752px;top:4243px;width:94px;height:28px;font-size:10px">SUBSCRIBE</div>

<div class="social-foot"><span style="left:467px"></span><span style="left:538px"></span><span style="left:618px"></span><span style="left:696px"></span></div>
<div class="abs center" style="left:0;top:4444px;width:1200px;font-size:9px;color:#fff">Copyright 2020 <span style="color:var(--orange)">Summit Builders</span> All Rights And Reserved</div>

</body>
</html>
```